Business Card for my New Brokerage

Looking to get a business card design for my new Real Estate Brokerage.
I want it with Picture, Phone Number, Email, Website, Office Address
Name and Designation. Please add logo too.

Target Market(s)

Real Estate Investors or Home Buyers

Industry/Entity Type

Real Estate

Contact Information for Business Card

Name, Email, Phone Number, website, email, office address

Colors
EB3D1F
EC4F4E
F09395
F8D3D4
FCEDEE

Requirements
Must have
• Minimalistic, Clean, Modern, Photo
Nice to have
• White and Red Colors

```html
<!DOCTYPE html>
<html lang="en">
<head>
<meta charset="utf-8">
<title>Ember Realty – Business Card</title>
<link href="https://fonts.googleapis.com/css2?family=Montserrat:wght@400;500;600;800&display=swap" rel="stylesheet">
<style>
  :root{
    --red:#e10a0a;
    --red-deep:#c80000;
    --red-light:#ef3a36;
    --gold:#d9b25a;
    --ink:#1c1c1c;
    --paper:#ffffff;
    --stage:#2e2e2e;
    --photo-a:#d6d6d6;
    --photo-b:#b9b9b9;
  }
  *{margin:0;padding:0;box-sizing:border-box}
  html,body{width:1200px;height:866px;overflow:hidden}
  body{background:var(--stage);font-family:"Montserrat",sans-serif;position:relative}
  .card{position:absolute;left:250px;width:700px;height:400px;overflow:hidden;border-radius:4px;box-shadow:0 8px 24px rgba(0,0,0,.45)}
  .card--front{top:22px;background:var(--paper)}
  .card--back{top:444px;background:radial-gradient(circle at 45% 45%,var(--red-light) 0%,var(--red) 45%,var(--red-deep) 100%)}

  .brand{position:absolute;display:flex;align-items:center;gap:10px;font-weight:800;letter-spacing:1px;white-space:nowrap}
  .brand__mark{display:inline-block;background:currentColor}
  .card--front .brand{left:40px;top:36px;font-size:42px;color:var(--red)}
  .card--front .brand__mark{width:12px;height:12px}
  .card--back .brand{left:50%;top:50%;transform:translate(-50%,-50%);font-size:68px;color:var(--paper)}
  .card--back .brand__mark{width:18px;height:18px}

  .person{position:absolute;left:40px;top:118px}
  .person__name{font-size:26px;font-weight:800;color:var(--red);letter-spacing:.5px}
  .person__role{font-size:16px;font-weight:500;color:var(--ink);margin-top:2px}

  .contacts{position:absolute;left:40px;top:198px;list-style:none;font-size:15px;font-weight:500;color:var(--ink)}
  .contacts li{display:flex;align-items:center;gap:10px;margin-bottom:8px}
  .contacts svg{width:16px;height:16px;flex:none}

  .rule{position:absolute;left:40px;top:272px;width:330px;height:1.5px;background:var(--red)}

  .portrait{position:absolute;right:40px;top:58px;width:250px;height:222px;border-radius:22px;background:linear-gradient(160deg,var(--photo-a),var(--photo-b))}

  .address{position:absolute;right:40px;top:292px;text-align:right;font-size:13px;font-weight:500;color:var(--ink);line-height:1.45}

  .footer-band{position:absolute;left:0;bottom:0;width:700px;height:70px}
  .website{position:absolute;right:40px;bottom:14px;font-size:15px;font-weight:600;color:var(--paper);letter-spacing:.5px}
</style>
</head>
<body>

<section class="card card--front" aria-label="Business card front">
  <div class="brand"><span>EMBER REALTY</span><span class="brand__mark"></span></div>

  <div class="person">
    <h1 class="person__name">MARCUS BENNETT</h1>
    <p class="person__role">Managing Director</p>
  </div>

  <ul class="contacts">
    <li>
      <svg viewBox="0 0 24 24" aria-hidden="true"><path fill="#e10a0a" d="M6.6 10.8a15.1 15.1 0 0 0 6.6 6.6l2.2-2.2a1 1 0 0 1 1-.25 11.4 11.4 0 0 0 3.6.57 1 1 0 0 1 1 1V20a1 1 0 0 1-1 1A17 17 0 0 1 3 4a1 1 0 0 1 1-1h3.5a1 1 0 0 1 1 1c0 1.25.2 2.45.57 3.57a1 1 0 0 1-.25 1z"/></svg>
      044-555 010 234
    </li>
    <li>
      <svg viewBox="0 0 24 24" aria-hidden="true"><rect x="2" y="5" width="20" height="14" fill="#e10a0a"/><path d="M2 5l10 8 10-8" fill="none" stroke="#fff" stroke-width="1.6"/></svg>
      info@emberrealty.com
    </li>
  </ul>

  <div class="rule"></div>

  <div class="portrait" role="img" aria-label="Portrait photo of the agent in a dark suit"></div>

  <address class="address" style="font-style:normal">
    17, Harbour Lane Office Park<br>45210, Country Name
  </address>

  <svg class="footer-band" viewBox="0 0 700 70" preserveAspectRatio="none" aria-hidden="true">
    <path d="M0 28 L320 44 C350 45 362 18 395 18 L700 18 L700 22 L395 22 C366 22 354 49 320 49 L0 33Z" fill="var(--gold)"/>
    <path d="M0 36 L320 53 C352 54 364 26 396 26 L700 26 L700 70 L0 70Z" fill="var(--red)"/>
  </svg>
  <p class="website">www.emberrealty.com</p>
</section>

<section class="card card--back" aria-label="Business card back">
  <div class="brand"><span>EMBER REALTY</span><span class="brand__mark"></span></div>
</section>

</body>
</html>
```